Website Needs Designing / Populating

We are a Business Consultancy in London. We are Headhunters and Recruitment. I have bought the Domain, and Wordpress Site, installed a template from Brindle Orchard. I have tried to do it myself but do not have the time to complete or do it as I want / need.
I have some 'stock' pics and a logo - see uploaded logo files.
I want an easy to use Website - tells clients and viewers what we are about.
We are a recruitment / Headhunting Consultancy so some visitors may want to apply for positions through loading their CV / Details through the site.
We want to be about friendly but expertise. Honest and trustworthy with a heavy emphasis on Consultancy!

Target Market(s)

Ledgerline Job Seekers. Our clients are in the Marketing Communications sectors so needs to be appealing to that market

Industry/Entity Type

Business Consultant

Number of Pages Required

3 page

Requirements
Must have
• Our Logo as a central theme - see uploaded files
Nice to have
• Simple. Easy to use, inviting

```html
<!DOCTYPE html>
<html lang="en">
<head>
<meta charset="utf-8">
<title>Ledgerline Recruitment</title>
<link href="https://fonts.googleapis.com/css2?family=Raleway:wght@400;500;600;700&family=Open+Sans:wght@400;600&display=swap" rel="stylesheet">
<style>
:root{
  --hero-top:#2a8ad4;
  --hero-bottom:#0d5ea9;
  --white:#ffffff;
  --navy:#1d3452;
  --ink:#555b62;
  --muted:#7a8087;
  --link:#1a8ac9;
  --yellow:#f8c20f;
  --purple:#6b2f8a;
  --blue:#1c87cf;
  --button:#1784d0;
  --band:#f3f3f3;
  --band-line:#dcdcdc;
  --client:#8d8d8d;
  --footer:#6b6b6b;
  --footer-text:#f4f4f4;
  --footer-muted:#d4d4d4;
}
*{box-sizing:border-box;margin:0;padding:0}
html,body{width:820px;height:1200px;overflow:hidden;background:var(--white)}
body{position:relative;font-family:"Open Sans",Arial,sans-serif;color:var(--ink)}
.abs{position:absolute}

.hero{left:0;top:0;width:820px;height:410px;background:linear-gradient(160deg,var(--hero-top),var(--hero-bottom))}
.brand{left:102px;top:20px;color:var(--white);font-family:"Raleway",sans-serif}
.brand-name{font-size:27px;font-weight:600;letter-spacing:-.5px;line-height:1}
.brand-sub{font-size:10px;font-weight:500;letter-spacing:9.4px;margin-top:4px}
.nav{top:38px;right:107px;display:flex;gap:24px}
.nav a{color:var(--white);text-decoration:none;font:400 12px Arial,sans-serif;letter-spacing:.1px}
.hero-kicker{left:0;width:820px;top:176px;text-align:center;color:var(--white);font:400 20px "Raleway",sans-serif}
.hero-title{left:0;width:820px;top:202px;text-align:center;color:var(--white);font:500 28px "Raleway",sans-serif;letter-spacing:.3px}
.dots{left:382px;top:353px;display:flex;gap:2px}
.dots span{width:12px;height:12px;border-radius:50%;background:var(--white)}
.dots .on{background:var(--yellow);box-shadow:inset 0 0 0 2px var(--white)}

.service{top:378px;width:199px;height:162px}
.service-photo{height:97px;background:linear-gradient(135deg,#d9dde3,#a9b2bd)}
.service-body{height:65px;text-align:center;color:var(--white);padding-top:12px}
.service-body h3{font:500 11.5px Arial,sans-serif;margin-bottom:4px}
.service-body p{font-size:7.4px;line-height:11.5px;opacity:.9}
.s-yellow .service-body{background:var(--yellow);color:#3a3320}
.s-yellow .service-body p{color:#6b5a1b}
.s-purple .service-body{background:var(--purple)}
.s-blue .service-body{background:var(--blue)}

.about{left:109px;top:583px;width:360px}
.about h2{font:400 22px "Raleway",sans-serif;color:var(--navy);margin-bottom:10px}
.about .lead{font-size:8.8px;line-height:16px;margin-bottom:7px}
.about .body{width:352px;font-size:7.5px;line-height:16px;color:var(--muted)}

.jobs{left:488px;top:590px;width:230px}
.jobs h2{font:400 17.5px "Raleway",sans-serif;color:var(--navy)}
.jobs-icon{left:-4px;top:30px}
.jobs-text{left:61px;top:28px;width:162px;font-size:7.6px;line-height:16px;color:var(--muted)}
.jobs-btn{left:60px;top:83px;width:71px;height:21px;background:var(--button);border-radius:2px;color:var(--white);font:400 7.2px Arial,sans-serif;display:flex;align-items:center;justify-content:center;gap:6px}

.clients{left:0;top:753px;width:820px;height:166px;background:var(--band);border-top:1px solid var(--band-line);border-bottom:1px solid var(--band-line)}
.clients h2{position:absolute;left:0;width:820px;top:40px;text-align:center;font:400 19px "Raleway",sans-serif;color:#666}
.client-row{position:absolute;left:118px;top:84px;width:584px;display:flex;justify-content:space-between;align-items:center}
.client{font:700 17px "Raleway",sans-serif;color:var(--client);display:flex;align-items:center;gap:5px}
.client i{display:inline-block;width:9px;height:9px;background:var(--client);border-radius:50%}

.projects{left:107px;top:962px;width:620px}
.projects h2{font:400 19px "Raleway",sans-serif;color:#3a3f45}
.project{top:41px;width:190px}
.project h3{font:400 10.5px "Raleway",sans-serif;color:var(--link);line-height:13px;margin-bottom:8px}
.project p{width:172px;font-size:7.4px;line-height:13.2px;color:var(--muted)}

.footer{left:0;top:1119px;width:820px;height:81px;background:var(--footer)}
.footer-nav{left:102px;top:22px;display:flex;gap:18px}
.footer-nav a{color:var(--footer-text);text-decoration:none;font:400 11px Arial,sans-serif}
.footer-copy{left:102px;top:45px;font-size:7.4px;color:var(--footer-muted)}
.social{left:646px;top:19px;display:flex;gap:2px}
.social span{width:16px;height:16px;border:1.2px solid var(--footer-text);border-radius:50%}
</style>
</head>
<body>

<header class="abs hero" role="img" aria-label="Blue tinted photo of business people reviewing charts on paper">
</header>
<div class="abs brand"><div class="brand-name">Ledgerline</div><div class="brand-sub">Recruitment</div></div>
<nav class="abs nav"><a href="#">ABOUT</a><a href="#">SERVICES</a><a href="#">TESTIMONIAL</a><a href="#">FIND JOB</a><a href="#">CONTACT</a></nav>
<p class="abs hero-kicker">Pellentesque faucibus accumsan</p>
<h1 class="abs hero-title">IT &amp; Finance Consulting &amp; Recruitment</h1>
<div class="abs dots"><span class="on"></span><span></span><span></span><span></span></div>

<section class="abs service s-yellow" style="left:100px">
  <div class="service-photo" role="img" aria-label="Photo of a consultant meeting with colleagues at a laptop"></div>
  <div class="service-body"><h3>BUSINESS CONSULTACY</h3><p>Mauris vel lacus vitae felis vestibulum volutpat<br>Eeu imperdiet ac nisl Cum socii</p></div>
</section>
<section class="abs service s-purple" style="left:308px">
  <div class="service-photo" role="img" aria-label="Photo of a handshake between a recruiter and a candidate"></div>
  <div class="service-body"><h3>RECRUITMENT</h3><p>Mauris vel lacus vitae felis vestibulum volutpat<br>Eeu imperdiet ac nisl Cum socii</p></div>
</section>
<section class="abs service s-blue" style="left:517px">
  <div class="service-photo" role="img" aria-label="Photo of a finance adviser speaking with a client in an office"></div>
  <div class="service-body"><h3>FINANCE SERVICES</h3><p>Mauris vel lacus vitae felis vestibulum volutpat<br>Eeu imperdiet ac nisl Cum socii</p></div>
</section>

<section class="abs about">
  <h2>About Ledgerline</h2>
  <p class="lead">Mauris vel lacus vitae felis vestibulum volutpat mperdiet ac nisl Cum sociis natoque penatibus et magnis dis parturient montes nascetur</p>
  <p class="body">Ridiculus mus In iaculis facilisis massa Etiam eu urna Sed porta Suspendisse quam leo molestie sed luctus quis feugiat in pede Fusce tellus Sed metus augue convallis et vehicula ut pulvinar eu ante IntDonec dictum lectus non odio Cras a ante</p>
</section>

<section class="abs jobs">
  <h2>Find a Financial Job</h2>
  <svg class="abs jobs-icon" width="58" height="58" viewBox="0 0 58 58" aria-hidden="true">
    <circle cx="29" cy="29" r="27.5" fill="#fff" stroke="#c9dff0" stroke-width="1.5"/>
    <circle cx="29" cy="29" r="24" fill="#1784d0"/>
    <circle cx="26" cy="26" r="10" fill="none" stroke="#fff" stroke-width="2.6"/>
    <circle cx="26" cy="23" r="3" fill="#fff"/>
    <path d="M20.5 31.5c1-3.5 3-5 5.5-5s4.5 1.5 5.5 5" fill="#fff"/>
    <line x1="33.5" y1="33.5" x2="40" y2="40" stroke="#fff" stroke-width="4" stroke-linecap="round"/>
  </svg>
  <p class="abs jobs-text">Auspendisse quam leo molestie sed luctus quis feugiat in pede Fusce tellus Sed metus augue convallis et vehicula ut</p>
  <a class="abs jobs-btn">CLICK HERE
    <svg width="5" height="7" viewBox="0 0 5 7" aria-hidden="true"><path d="M1 1l2.5 2.5L1 6" fill="none" stroke="#fff" stroke-width="1.1"/></svg>
  </a>
</section>

<section class="abs clients">
  <h2>Our Clients</h2>
  <div class="client-row">
    <span class="client">Kestrel</span>
    <span class="client"><i></i>Marlowe</span>
    <span class="client">Tessera</span>
    <span class="client">Ovando</span>
    <span class="client">Fernly</span>
    <span class="client">Halvard</span>
  </div>
</section>

<section class="abs projects">
  <h2>Latest Project</h2>
  <article class="abs project" style="left:2px">
    <h3>Mauris vel lacus vitae felis vestib ulum volutpat imperdiet</h3>
    <p>Sed porta Suspendisse quam leo molestie sed luctus quis feugiat in pede Fusce tellus Sed metus augue convallis et</p>
  </article>
  <article class="abs project" style="left:215px">
    <h3>Curabitur vel mi sit amet magna malesuada ultrices</h3>
    <p>Sed porta Suspendisse quam leo molestie sed luctus quis feugiat in pede Fusce tellus Sed metus augue convallis et vehicula</p>
  </article>
  <article class="abs project" style="left:425px">
    <h3>Aenean porttitor eros vel dolor Donec convallis pede venenatis nibh</h3>
    <p>Sed porta Suspendisse quam leo molestie sed luctus quis feugiat in pede Fusce tellus Sed metus augue convallis et vehicula</p>
  </article>
</section>

<footer class="abs footer">
  <nav class="abs footer-nav"><a href="#">HOME</a><a href="#">ABOUT</a><a href="#">SERVICES</a><a href="#">TESTIMONIAL</a><a href="#">FIND JOB</a><a href="#">CONTACT</a></nav>
  <p class="abs footer-copy">© 2016 Company Name &nbsp;All right reserved &nbsp;Term of Use</p>
  <div class="abs social" aria-label="Social links"><span></span><span></span><span></span><span></span></div>
</footer>

</body>
</html>
```